New Business Card Design Project

Use the flyer uploaded and website www.brightoakbuilders.com for inspiration.
List Our Services on Backside of business cards
Marcus Delling
Harborline Builders Inc.
Licensed General Contractors
858-471-6093

Contact Information for Business Card

Use the flyer uploaded and website www.brightoakbuilders.com for inspiration. List Our Services on Backside of business cards Marcus Delling Harborline Builders Inc. Licensed General Contractors 858-471-6093

```html
<!DOCTYPE html>
<html lang="en">
<head>
<meta charset="utf-8">
<title>Harborline Builders – Business Cards</title>
<link rel="stylesheet" href="https://fonts.googleapis.com/css2?family=Cinzel:wght@400;700&family=Montserrat:wght@400&display=swap">
<style>
  :root {
    --page-bg: #1b1b1d;
    --card-bg: #141416;
    --ink: #f4f4f4;
    --rule: #d9d9d9;
  }
  * { box-sizing: border-box; margin: 0; padding: 0; }
  html, body { width: 1200px; height: 912px; overflow: hidden; }
  body {
    background: var(--page-bg);
    position: relative;
    font-family: "Montserrat", sans-serif;
    color: var(--ink);
  }
  .card {
    position: absolute;
    width: 630px;
    height: 360px;
    background: var(--card-bg);
    border-radius: 16px;
    box-shadow: 0 18px 40px rgba(0,0,0,0.55);
  }
  .card--services { left: 110px; top: 56px; }
  .card--contact { left: 460px; top: 496px; }

  .brand {
    position: absolute;
    left: 0; right: 0;
    display: flex;
    justify-content: center;
    align-items: center;
    gap: 12px;
  }
  .brand__dot {
    width: 14px; height: 14px;
    border: 1.5px solid var(--ink);
    border-radius: 50%;
  }
  .brand__name {
    font-family: "Cinzel", serif;
    font-weight: 400;
    font-size: 30px;
    letter-spacing: 1px;
  }
  .card--services .brand { top: 118px; }
  .card--contact .brand { top: 52px; }

  .services {
    position: absolute;
    left: 0; right: 0; top: 210px;
    text-align: center;
    font-size: 17px;
    line-height: 30px;
    letter-spacing: 0.3px;
  }

  .person {
    position: absolute;
    right: 340px; top: 150px;
    text-align: right;
  }
  .person__name {
    font-family: "Cinzel", serif;
    font-weight: 700;
    font-size: 25px;
    letter-spacing: 1px;
  }
  .person__role { font-size: 15px; margin-top: 4px; }

  .divider {
    position: absolute;
    left: 306px; top: 136px;
    width: 1px; height: 92px;
    background: var(--rule);
  }
  .contact {
    position: absolute;
    left: 326px; top: 138px;
    list-style: none;
    font-size: 14px;
  }
  .contact li { display: flex; align-items: center; gap: 10px; height: 30px; }
  .contact svg { width: 14px; height: 14px; fill: var(--ink); flex: none; }

  .footer {
    position: absolute;
    left: 0; right: 0; bottom: 40px;
    display: flex;
    align-items: center;
    gap: 14px;
    padding: 0 0 0 40px;
    font-size: 15px;
  }
  .footer__rule { height: 1px; background: var(--rule); flex: 1; }
  .footer__rule--end { flex: 0 0 150px; }
</style>
</head>
<body>

  <section class="card card--services">
    <div class="brand">
      <span class="brand__dot"></span>
      <span class="brand__name">HARBORLINE BUILDERS</span>
    </div>
    <p class="services">
      Painting • Flooring • Kitchens • Custom Renovations<br>
      Bathrooms • Energy Efficienct Upgrades
    </p>
  </section>

  <section class="card card--contact">
    <div class="brand">
      <span class="brand__dot"></span>
      <span class="brand__name">HARBORLINE BUILDERS</span>
    </div>

    <div class="person">
      <p class="person__name">MARCUS DELLING</p>
      <p class="person__role">Licensed General Contractors</p>
    </div>

    <span class="divider"></span>

    <ul class="contact">
      <li>
        <svg viewBox="0 0 24 24"><path d="M6.6 10.8a15.1 15.1 0 0 0 6.6 6.6l2.2-2.2a1 1 0 0 1 1-.25 11.4 11.4 0 0 0 3.6.57 1 1 0 0 1 1 1V20a1 1 0 0 1-1 1A17 17 0 0 1 3 4a1 1 0 0 1 1-1h3.5a1 1 0 0 1 1 1c0 1.25.2 2.45.57 3.57a1 1 0 0 1-.25 1z"/></svg>
        858-471-6093
      </li>
      <li>
        <svg viewBox="0 0 24 24"><path d="M2 5h20v14H2zM3.5 6.5 12 13l8.5-6.5v-.01H3.5z"/></svg>
        info@brightoakbuilders.com
      </li>
      <li>
        <svg viewBox="0 0 24 24"><path d="M12 2a10 10 0 1 0 0 20 10 10 0 0 0 0-20zm0 2c1 1.3 1.8 3 2.2 5H9.8c.4-2 1.2-3.7 2.2-5zM4.3 14a8 8 0 0 1 0-4h3.3a16 16 0 0 0 0 4zm5.5 0a14 14 0 0 1 0-4h4.4a14 14 0 0 1 0 4zm6.6 0a16 16 0 0 0 0-4h3.3a8 8 0 0 1 0 4zM12 20c-1-1.3-1.8-3-2.2-5h4.4c-.4 2-1.2 3.7-2.2 5z"/></svg>
        www.brightoakbuilders.com
      </li>
    </ul>

    <div class="footer">
      <span class="footer__rule"></span>
      <span>Harborline Builders Inc.</span>
      <span class="footer__rule footer__rule--end"></span>
    </div>
  </section>

</body>
</html>
```